Restyle corporate identity (+ logo) for a road construction company

We need a new logo and stationary design for our company VARNOK path. VARNOK path® increases the road base strength, while reducing major costs and time of road construction. Attached some examples of the current design.

Our wishes for the new logo:
- Business look
- Style sheet
- Modern

More information: www.varnokpath.example
Updates

Target Market(s)

Government

Industry/Entity Type

Construction

Requirements
Must have
• Logo (with road sign) + text

```html
<!DOCTYPE html>
<html lang="en">
<head>
<meta charset="utf-8">
<title>VARNOK path – Business Cards</title>
<link rel="stylesheet" href="https://fonts.googleapis.com/css2?family=Source+Sans+3:wght@400;600&display=swap">
<style>
  :root {
    --backdrop: #e4e5e7;
    --card-white: #f1f1f3;
    --brand-blue: #0f7be0;
    --text-dark: #4a4c50;
    --text-light: #ffffff;
    --url-tint: #d9ebfb;
  }
  * { margin: 0; padding: 0; box-sizing: border-box; }
  html, body {
    width: 1105px;
    height: 1200px;
    overflow: hidden;
    background: var(--backdrop);
    font-family: "Source Sans 3", Arial, sans-serif;
  }
  .canvas {
    position: relative;
    width: 1105px;
    height: 1200px;
  }
  .card {
    position: absolute;
    left: 182px;
    width: 746px;
    height: 424px;
    overflow: hidden;
  }
  .card--front { top: 120px; background: var(--card-white); }
  .card--back  { top: 636px; background: var(--brand-blue); }

  .address {
    position: absolute;
    left: 52px;
    top: 50px;
    font-size: 20px;
    line-height: 27px;
    color: var(--text-dark);
  }
  .name-band {
    position: absolute;
    left: 0;
    top: 163px;
    width: 408px;
    height: 97px;
    background: var(--brand-blue);
    border-radius: 0 14px 14px 0;
    color: var(--text-light);
    padding: 20px 0 0 52px;
  }
  .name-band__name {
    font-size: 27px;
    font-weight: 600;
    letter-spacing: 0.5px;
    line-height: 30px;
  }
  .name-band__role {
    font-size: 20px;
    line-height: 27px;
  }
  .wordmark {
    position: absolute;
    display: flex;
    align-items: center;
    font-weight: 600;
    white-space: nowrap;
  }
  .wordmark__square {
    flex: none;
    border-radius: 4px;
  }
  .wordmark--front {
    left: 428px;
    top: 182px;
    font-size: 46px;
    line-height: 60px;
    color: var(--brand-blue);
    gap: 14px;
  }
  .wordmark--front .wordmark__square {
    width: 26px; height: 26px;
    background: var(--brand-blue);
  }
  .wordmark--back {
    left: 0;
    right: 0;
    top: 180px;
    justify-content: center;
    font-size: 62px;
    line-height: 70px;
    color: var(--text-light);
    gap: 18px;
  }
  .wordmark--back .wordmark__square {
    width: 34px; height: 34px;
    background: var(--text-light);
  }
  .contacts {
    position: absolute;
    left: 52px;
    top: 294px;
    list-style: none;
    font-size: 20px;
    line-height: 28.5px;
    color: var(--text-dark);
  }
  .contacts__item {
    display: flex;
    align-items: center;
    gap: 9px;
  }
  .contacts__icon {
    width: 17px;
    height: 17px;
    flex: none;
    fill: var(--brand-blue);
  }
  .back-url {
    position: absolute;
    left: 0;
    right: 0;
    top: 356px;
    text-align: center;
    font-size: 20px;
    letter-spacing: 4px;
    color: var(--url-tint);
  }
</style>
</head>
<body>
<main class="canvas">

  <section class="card card--front" aria-label="Business card front">
    <address class="address">
      Brederolaan 214<br>
      2611 HT Delft<br>
      The Netherlands
    </address>

    <div class="name-band">
      <p class="name-band__name">LIAM VERHOEF</p>
      <p class="name-band__role">CEO/Founder</p>
    </div>

    <div class="wordmark wordmark--front">
      <span class="wordmark__square"></span>
      <span class="wordmark__text">VARNOK path</span>
    </div>

    <ul class="contacts">
      <li class="contacts__item">
        <svg class="contacts__icon" viewBox="0 0 24 24" aria-hidden="true"><path d="M6.6 10.8a15.1 15.1 0 0 0 6.6 6.6l2.2-2.2a1 1 0 0 1 1-.25 11.4 11.4 0 0 0 3.6.57 1 1 0 0 1 1 1V20a1 1 0 0 1-1 1A17 17 0 0 1 3 4a1 1 0 0 1 1-1h3.5a1 1 0 0 1 1 1c0 1.25.2 2.45.57 3.6a1 1 0 0 1-.25 1z"/></svg>
        <span>555 014 2298</span>
      </li>
      <li class="contacts__item">
        <svg class="contacts__icon" viewBox="0 0 24 24" aria-hidden="true"><path d="M2 5h20v14H2z M2 5l10 8 10-8" fill="none" stroke="#0f7be0" stroke-width="0"/><path d="M2 6.2 12 13l10-6.8V19H2z"/><path d="M2 5h20l-10 6.8z"/></svg>
        <span>info@varnokpath.example</span>
      </li>
      <li class="contacts__item">
        <svg class="contacts__icon" viewBox="0 0 24 24" aria-hidden="true"><circle cx="12" cy="12" r="10"/><path d="M4 12h16M12 2c3 3 3 17 0 20M12 2c-3 3-3 17 0 20" fill="none" stroke="#f1f1f3" stroke-width="1.6"/></svg>
        <span>www.varnokpath.example</span>
      </li>
    </ul>
  </section>

  <section class="card card--back" aria-label="Business card back">
    <div class="wordmark wordmark--back">
      <span class="wordmark__square"></span>
      <span class="wordmark__text">VARNOK path</span>
    </div>
    <p class="back-url">www.varnokpath.example</p>
  </section>

</main>
</body>
</html>
```